Verpackungsdesign für hochwertigs Nahrungsergänzungmittel
Zielgruppe
Nahrungsergänzungsmittel aus hochwertigen Zutaten , werden in Deutschland gefertigt. Unsere Produkte sollen sowohl Jung als auch Alt ansprechen dabei modern und zugleich auch medizinisch Wirkung ausstrahlen und vertrauen erwecken da diese auch in der Apotheke verkauft werden.
kurzes Update zum Briefing:
Am Anfang ist eine Mischung aus verschiedenen Suppliments. Wir denken aber weiter und wollen ein Design das mehrere Suppliments abdeckt wie z.b. auch Kalium, Magnesium etc. von daher soll das Design alles abdecken, schlicht aber auch zugleich ansprechend und natürlich sein. Die Marke nennt sich Wiesgrund.
Es wird sowohl im Direktvertrieb, wie auch Online und in der Apotheke angeboten
Aufgabenstellung
Das Produkt soll Nachhaltigkeit suggerieren, sowie gute Qualität der Inhaltsstoffe. Das Produkt ist in einer Faltschachtel.

```html
<!DOCTYPE html>
<html lang="de">
<head>
<meta charset="utf-8">
<title>Wiesgrund – Luno Night Faltschachtel</title>
<link href="https://fonts.googleapis.com/css2?family=Raleway:wght@300;400;800&display=swap" rel="stylesheet">
<style>
  :root {
    --stage: #a79fb9;
    --carton: #ecebe8;
    --carton-side: #dedcd9;
    --ink: #3f3d42;
    --violet: #5e4e80;
    --violet-deep: #4d3e6c;
    --glow: rgba(110, 92, 150, 0.75);
    --white: #f4f3f1;
  }
  * { box-sizing: border-box; margin: 0; padding: 0; }
  html, body {
    width: 667px; height: 1200px; overflow: hidden;
    background: var(--stage);
    font-family: "Raleway", sans-serif;
    color: var(--ink);
  }
  .carton {
    position: absolute; left: 88px; top: 170px;
    width: 490px; height: 860px;
    display: flex;
  }
  .side-panel {
    width: 90px; height: 100%;
    background: var(--carton-side);
    display: flex; flex-direction: column;
  }
  .side-badges {
    flex: 1;
    display: flex; flex-direction: column; align-items: center;
    justify-content: space-evenly; padding: 40px 0;
  }
  .badge {
    display: flex; flex-direction: column; align-items: center; gap: 5px;
  }
  .badge-ring {
    width: 52px; height: 52px; border-radius: 50%;
    border: 2px solid var(--violet);
  }
  .badge-label {
    width: 80px; text-align: center;
    font-size: 9px; font-weight: 400; line-height: 1.2; color: var(--ink);
  }
  .side-band {
    height: 150px; background: var(--violet-deep);
    color: var(--white);
    display: flex; align-items: center; justify-content: center;
    text-align: center; font-size: 15px; font-weight: 400; line-height: 1.35;
  }
  .front-panel {
    position: relative; flex: 1; height: 100%;
    background: var(--carton);
    display: flex; flex-direction: column;
  }
  .front-body { position: relative; flex: 1; }
  .product-name {
    position: absolute; left: 52px; top: 95px;
    font-size: 50px; font-weight: 400; line-height: 1.05;
    letter-spacing: 0.5px;
  }
  .aura {
    position: absolute; left: 50%; top: 420px;
    width: 400px; height: 400px; transform: translate(-50%, -50%);
    border-radius: 50%;
    background: radial-gradient(circle, var(--glow) 0%, rgba(110,92,150,0.45) 30%, rgba(110,92,150,0) 68%);
  }
  .brand-seal {
    position: absolute; left: 50%; top: 420px;
    width: 170px; height: 170px; transform: translate(-50%, -50%);
    border-radius: 50%; background: var(--white);
    display: flex; align-items: center; justify-content: center;
    font-size: 24px; font-weight: 800; color: var(--violet);
  }
  .claim {
    position: absolute; left: 0; right: 0; top: 615px;
    text-align: center; font-size: 18px; font-weight: 300; line-height: 1.35;
  }
  .front-band {
    height: 150px; background: var(--violet);
    display: flex; align-items: center; justify-content: center;
  }
  .brand-name {
    color: var(--white); font-size: 32px; font-weight: 800; letter-spacing: 0.3px;
  }
</style>
</head>
<body>
  <div class="carton">
    <aside class="side-panel">
      <div class="side-badges">
        <div class="badge"><div class="badge-ring"></div><span class="badge-label">vegan</span></div>
        <div class="badge"><div class="badge-ring"></div><span class="badge-label">made in germany</span></div>
        <div class="badge"><div class="badge-ring"></div><span class="badge-label">ohne künstliche Zusatzstoffe</span></div>
      </div>
      <div class="side-band">50 Stück<br>à 10 mg</div>
    </aside>
    <section class="front-panel">
      <div class="front-body">
        <h1 class="product-name">LUNO<br>NIGHT</h1>
        <div class="aura"></div>
        <div class="brand-seal">Wiesgrund</div>
        <p class="claim">Nahrungsergänzung für<br>erholsamen Schlaf<br>Mit Magnesium &amp; Melatonin</p>
      </div>
      <div class="front-band"><span class="brand-name">Wiesgrund</span></div>
    </section>
  </div>
</body>
</html>
```